Layout for site fence advertising - length approx. 250 cm x 125 cm

The advertising will later be printed on a PVC film and used for events or on sports fields.

Main services :
Your regional contact at
Real estate and business financing
independent insurance advice

```html
<!DOCTYPE html>
<html lang="de">
<head>
<meta charset="utf-8">
<title>Halden Vermögensberatung – Bauzaunbanner</title>
<link href="https://fonts.googleapis.com/css2?family=Teko:wght@500;600&family=Nunito:wght@600;700&display=swap" rel="stylesheet">
<style>
  :root {
    --brand-blue: #1a56bb;
    --paper-white: #ffffff;
    --stage-grey: #3a3a3a;
    --photo-dark: #3b2a22;
    --photo-mid: #8a6e5c;
    --photo-light: #e9e6e2;
    --suit-navy: #22243a;
  }
  html, body {
    margin: 0;
    padding: 0;
    width: 1000px;
    height: 1200px;
    overflow: hidden;
    background: var(--stage-grey);
  }
  .banner {
    position: absolute;
    left: 30px;
    top: 365px;
    width: 940px;
    height: 470px;
    background: var(--brand-blue);
    overflow: hidden;
    color: var(--paper-white);
    box-shadow: 0 10px 40px rgba(0,0,0,0.45);
  }
  .banner__backdrop {
    position: absolute;
    inset: 0;
  }
  .brand {
    position: absolute;
    left: 33px;
    top: 43px;
    height: 114px;
    display: flex;
    align-items: center;
  }
  .brand__circle {
    width: 106px;
    height: 106px;
    border: 3px solid var(--paper-white);
    border-radius: 50%;
    box-sizing: border-box;
  }
  .brand__divider {
    width: 3px;
    height: 114px;
    background: var(--paper-white);
    margin: 0 8px 0 17px;
  }
  .brand__name {
    font-family: "Nunito", sans-serif;
    font-weight: 700;
    font-size: 21px;
    line-height: 1.2;
    margin: 0;
  }
  .brand__tagline {
    font-family: "Nunito", sans-serif;
    font-weight: 600;
    font-size: 15.5px;
    margin: 3px 0 0;
  }
  .services {
    position: absolute;
    left: 32px;
    top: 203px;
    font-family: "Teko", sans-serif;
    text-transform: uppercase;
  }
  .services__title {
    margin: 0 0 4px;
    font-weight: 600;
    font-size: 38px;
    line-height: 1;
    letter-spacing: 2.5px;
  }
  .services__list {
    list-style: none;
    margin: 0;
    padding: 0;
    font-weight: 500;
    font-size: 27px;
    line-height: 32px;
    letter-spacing: 0.8px;
  }
  .services__list li::before {
    content: "•";
    margin-right: 6px;
  }
  .web {
    position: absolute;
    left: 32px;
    top: 397px;
    width: 468px;
    border-top: 1.5px solid var(--paper-white);
    padding-top: 6px;
    font-family: "Teko", sans-serif;
    font-weight: 600;
    font-size: 38px;
    line-height: 1;
    letter-spacing: 7.4px;
    white-space: nowrap;
  }
</style>
</head>
<body>
  <section class="banner">
    <svg class="banner__backdrop" width="940" height="470" viewBox="0 0 940 470">
      <defs>
        <linearGradient id="portraitTones" x1="0" y1="0" x2="1" y2="1">
          <stop offset="0" stop-color="var(--photo-dark)"/>
          <stop offset="0.35" stop-color="var(--photo-light)"/>
          <stop offset="0.6" stop-color="var(--photo-mid)"/>
          <stop offset="1" stop-color="var(--suit-navy)"/>
        </linearGradient>
      </defs>
      <rect x="650" y="0" width="290" height="470" fill="var(--paper-white)"/>
      <circle cx="708" cy="235" r="245" fill="var(--paper-white)"/>
      <circle cx="725" cy="238" r="222" fill="url(#portraitTones)" role="img" aria-label="Portrait of the financial advisor in a dark suit and white shirt"/>
    </svg>

    <header class="brand">
      <div class="brand__circle"></div>
      <div class="brand__divider"></div>
      <div class="brand__text">
        <p class="brand__name">Halden Vermögensberatung GmbH</p>
        <p class="brand__tagline">Finanzieren, Versichern, Vorsorgen</p>
      </div>
    </header>

    <div class="services">
      <h2 class="services__title">Main services :</h2>
      <ul class="services__list">
        <li>Your regional contact at</li>
        <li>Real estate and business financing</li>
        <li>Independent insurance advice</li>
      </ul>
    </div>

    <div class="web">www.yourwebsite.com</div>
  </section>
</body>
</html>
```